Business Card- Can you make it cool vs boring!

Need a refresh on my business card! Want it to be modern but simple, classic and a pop of coolness! we do senior living and it is boring. but that doesn't mean our business card have to look boring! Open to two sided cards. our website is www.Dunmere-PK.com

Target Market(s)

capital market

Industry/Entity Type

senior housing/ real estate

Contact Information for Business Card

logo/ name/ cell/ address/ www.Dunmere-PK.com/ space for a QR code

Requirements
Must have
• maybe a QR code (do not make prominent I may not use the QR so design where it can be taken out) that link to more about us/ landing page. needs to be modern but clean
Should not have
• clip art or script

```html
<!DOCTYPE html>
<html lang="en">
<head>
<meta charset="utf-8">
<title>Dunmere Park – Business Card</title>
<link href="https://fonts.googleapis.com/css2?family=Montserrat:wght@400;500;700&display=swap" rel="stylesheet">
<style>
  :root {
    --stage: #2d2d2d;
    --rust: #bb4d26;
    --paper: #ffffff;
    --ink: #222222;
    --soft-white: #f4efec;
  }
  * { margin: 0; padding: 0; box-sizing: border-box; }
  html, body {
    width: 1200px; height: 565px; overflow: hidden;
    background: var(--stage);
    font-family: "Montserrat", Arial, sans-serif;
  }
  .card {
    position: absolute; top: 130px;
    width: 531px; height: 304px;
    border-radius: 20px; overflow: hidden;
    box-shadow: 0 6px 14px rgba(0,0,0,0.45);
  }
  .card--front { left: 62px; background: var(--paper); }
  .card--back { left: 607px; background: var(--rust); }

  .front-band { position: absolute; inset: 0; width: 100%; height: 100%; }

  .holder { position: absolute; left: 20px; top: 38px; color: var(--paper); }
  .holder__name { font-weight: 700; font-size: 21px; letter-spacing: 0.2px; line-height: 1.1; }
  .holder__title { font-weight: 400; font-size: 14px; margin-top: 6px; }

  .brand-name {
    position: absolute; right: 22px; top: 44px;
    color: var(--rust); font-weight: 500; font-size: 30px; letter-spacing: 0.5px;
  }

  .address {
    position: absolute; right: 21px; top: 156px;
    text-align: right; color: var(--ink); font-size: 14.5px; line-height: 21.5px;
  }
  .contacts {
    position: absolute; right: 21px; top: 205px;
    list-style: none; color: var(--ink); font-size: 14.5px; line-height: 21.5px;
  }
  .contacts li { display: flex; justify-content: flex-end; align-items: center; gap: 6px; }
  .contacts svg { width: 12px; height: 12px; fill: var(--rust); flex: none; }

  .back-texture { position: absolute; inset: 0; background: var(--rust); }
  .back-brand {
    position: absolute; inset: 0; display: flex; align-items: center; justify-content: center;
    color: var(--paper); font-weight: 500; font-size: 46px; letter-spacing: 0.5px;
  }
</style>
</head>
<body>
  <section class="card card--front">
    <svg class="front-band" viewBox="0 0 531 304" preserveAspectRatio="none" aria-hidden="true">
      <path d="M0 0 H301 C262 80 248 200 280 304 H0 Z" fill="var(--rust)"/>
    </svg>

    <div class="holder">
      <p class="holder__name">HAROLD BRISCO</p>
      <p class="holder__title">General Manager</p>
    </div>

    <p class="brand-name">Dunmere Park</p>

    <address class="address">
      4870 Cedar Hollow Drive, Suite 310<br>
      Marlow Springs, TX 77512
    </address>

    <ul class="contacts">
      <li>(555) 014-2287
        <svg viewBox="0 0 24 24" aria-hidden="true"><path d="M3 9c0-3 4-5 9-5s9 2 9 5v2h-4V9c-1-1-3-1.5-5-1.5S8 8 7 9v2H3z M6 12h12l2 8H4z"/></svg>
      </li>
      <li>info@Dunmere-PK.com
        <svg viewBox="0 0 24 24" aria-hidden="true"><path d="M2 5h20v14H2z M3 6l9 7 9-7" stroke="#fff" stroke-width="1.5"/></svg>
      </li>
      <li>www.Dunmere-PK.com
        <svg viewBox="0 0 24 24" aria-hidden="true"><circle cx="12" cy="12" r="10"/><path d="M2 12h20M12 2c3 3 3 17 0 20M12 2c-3 3-3 17 0 20" stroke="#fff" stroke-width="1.3" fill="none"/></svg>
      </li>
    </ul>
  </section>

  <section class="card card--back">
    <div class="back-texture" role="img" aria-label="Faint geometric lattice pattern in rust tones"></div>
    <p class="back-brand">Dunmere Park</p>
  </section>
</body>
</html>
```